4D Cradle Glimpse Luxury Ultrasound Billboard

Design a HIGH-END, MODERN billboard for my private prenatal ultrasound studio, 4D Cradle Glimpse, located in Pace, Florida.
This billboard will be viewed by drivers traveling at highway speeds, so it must be extremely clean, simple, and readable within 6 seconds.
About My Business
4D Cradle Glimpse is a private prenatal ultrasound studio specializing in:
Highest technology 4D/HD Ultrasounds
Early Gender Determination
Pregnancy Confirmation
I have been serving families for nearly 10 years and is known for creating a memorable experience, not just an ultrasound appointment.
Design Style
I DO NOT want:
Flowers
Leaves
Swirls
Glitter
Hearts everywhere
Busy backgrounds
Generic maternity stock graphics
I DO want:
Modern
Luxury
Upscale
Clean
Professional
Eye-catching
Premium medical spa feel
Colors
Use colors from my logo:
LOGO Green ( or a deep green)
Black
White
Soft Gold accents
Images:
Incorporate my professional headshot in a clean, modern way, logo, and the ultrasound images
Text
Keep wording minimal.
Primary Headline ( OPEN TO IDEAS) :
EXAMPLES ( WOULD RATHER SOMETHING MORE CATCHY)
" ADVANCED IMAGING. UNFORGETTABLE MOMENTS"
"MEET YOUR BABY BEFORE BIRTH"
Under headline:
4D Ultrasound • Early Gender • Pregnancy Confirmation
Business Name:
4D Cradle Glimpse
Private Prenatal Ultrasound Studio
Phone Number:
850-471-5923
Important
This billboard must be readable in 5–6 seconds from a moving vehicle.
Less text is better.
The phone number and business name must be visible from a distance.
The design should feel like a premium brand that immediately tells expecting parents:
“This is where I go to see my baby.”
Files Provided
Official logo
Headshot
Ultrasound images
Don’t make this look like a medical office billboard.
Make it look like a luxury baby experience billboard. That’s what separates 4D Cradle Glimpse from hospitals, OB offices, and all the new studios popping up around you. The emotional connection is what gets moms to book. ❤️
Billboard Size - 10.6” x 36”

```html
<!DOCTYPE html>
<html lang="en">
<head>
<meta charset="utf-8">
<title>4D Cradle Glimpse Billboard</title>
<link rel="stylesheet" href="https://fonts.googleapis.com/css2?family=Playfair+Display:wght@400;600&family=Roboto:wght@500;700&family=Montserrat:wght@500&display=swap">
<style>
  :root{
    --deep-green:#15271f;
    --ink:#132a21;
    --gold:#c3972f;
    --pin-gold:#f2b443;
    --frame-gold:#f0a830;
    --paper:#f2f4f3;
    --white:#ffffff;
    --logo-border:#6b7a74;
    --scan-dark:#5a1f14;
    --scan-mid:#a04a35;
    --scan-light:#c97a62;
    --skin:#d9bf98;
    --hair:#c6a77c;
    --scrubs:#4f6448;
    --studio:#e4e4e1;
  }
  *{margin:0;padding:0;box-sizing:border-box}
  html,body{width:1200px;height:767px;overflow:hidden;background:var(--white)}
  .board{position:absolute;left:10px;width:1182px;height:369px;overflow:hidden}
  .board--dark{top:13px;background:var(--deep-green);color:var(--white)}
  .board--light{top:386px;background:var(--paper);color:var(--ink)}
  .headline{position:absolute;left:0;width:100%;text-align:center;font-family:"Playfair Display",serif;font-weight:400;font-size:55px;line-height:1;letter-spacing:-0.8px}
  .headline--top{top:54px}
  .headline--bottom{top:112px;color:var(--gold)}
  .services{position:absolute;left:0;width:100%;top:188px;text-align:center;font-family:Roboto,sans-serif;font-weight:500;font-size:23.5px;line-height:26px}
  .services .dot{color:var(--pin-gold);margin:0 12px}
  .brand-box{position:absolute;left:342px;top:254px;width:206px;height:102px;background:var(--white);border:2px solid var(--logo-border);border-radius:12px;text-align:center;padding-top:22px}
  .brand-name{font-family:"Playfair Display",serif;font-weight:600;font-size:21px;color:var(--ink);line-height:1.1}
  .brand-rule{width:176px;height:1px;background:var(--gold);margin:12px auto 6px}
  .brand-tag{font-family:Montserrat,sans-serif;font-weight:500;font-size:8.6px;letter-spacing:0.6px;color:#3d4a45}
  .contact{position:absolute;left:594px;top:266px}
  .pin{position:absolute;left:0;top:0;width:20px;height:26px}
  .city{position:absolute;left:31px;top:0;font-family:Roboto,sans-serif;font-weight:500;font-size:22px;line-height:26px;white-space:nowrap}
  .phone{position:absolute;left:30px;top:28px;font-family:Roboto,sans-serif;font-weight:700;font-size:33px;line-height:38px;white-space:nowrap}
  .headshot{position:absolute}
  .board--dark .headshot{left:21px;top:7px;width:234px;height:362px;border-radius:110px 110px 0 0;background:radial-gradient(ellipse at 50% 30%,#e3c59a 0%,#b9956f 30%,#3f5a3c 62%,#2c4030 100%)}
  .board--light .headshot{left:820px;top:0;width:362px;height:369px;
    background:
      linear-gradient(90deg,var(--paper) 0%,rgba(242,244,243,0) 22%),
      radial-gradient(ellipse 28% 22% at 58% 30%,var(--skin) 0%,var(--hair) 60%,rgba(198,167,124,0) 100%),
      radial-gradient(ellipse 40% 46% at 58% 78%,var(--scrubs) 0%,#6d7f66 55%,rgba(109,127,102,0) 100%),
      linear-gradient(90deg,var(--paper) 0%,var(--studio) 45%,#d4d4d1 80%,#8f9290 100%);}
  .scan{position:absolute;border:3px solid var(--frame-gold);background:radial-gradient(ellipse at 30% 45%,var(--scan-light) 0%,var(--scan-mid) 40%,var(--scan-dark) 80%)}
  .board--dark .scan{left:935px;top:69px;width:231px;height:256px;transform:rotate(4deg)}
  .diagonal{position:absolute;left:0;top:0;width:250px;height:369px}
  .board--light .scan{left:31px;top:45px;width:207px;height:256px;transform:rotate(-15deg)}
</style>
</head>
<body>
  <section class="board board--dark">
    <div class="headshot" role="img" aria-label="Studio owner portrait in green scrubs holding an ultrasound probe"></div>
    <h1 class="headline headline--top">MEET YOUR BABY</h1>
    <h2 class="headline headline--bottom">BEFORE BIRTH</h2>
    <p class="services">4D Ultrasound<span class="dot">•</span>Pregnancy Confirmation<span class="dot">•</span>Early Gender</p>
    <div class="brand-box">
      <div class="brand-name">4D Cradle Glimpse</div>
      <div class="brand-rule"></div>
      <div class="brand-tag">PRENATAL ULTRASOUND STUDIO</div>
    </div>
    <div class="contact">
      <svg class="pin" viewBox="0 0 20 26"><path d="M10 0C4.5 0 0 4.4 0 9.8 0 17 10 26 10 26s10-9 10-16.2C20 4.4 15.5 0 10 0z" fill="var(--pin-gold)"/><circle cx="10" cy="9.5" r="3.6" fill="var(--deep-green)"/></svg>
      <div class="city">Cedar Bay Florida</div>
      <div class="phone">850-471-5923</div>
    </div>
    <div class="scan" role="img" aria-label="4D ultrasound image of twins"></div>
  </section>

  <section class="board board--light">
    <svg class="diagonal" viewBox="0 0 250 369" preserveAspectRatio="none"><polygon points="0,0 141,0 243,369 0,369" fill="var(--deep-green)"/></svg>
    <div class="scan" role="img" aria-label="4D ultrasound image of twins"></div>
    <div class="headshot" role="img" aria-label="Studio owner portrait in green scrubs beside ultrasound equipment in a bright studio"></div>
    <h1 class="headline headline--top">MEET YOUR BABY</h1>
    <h2 class="headline headline--bottom">BEFORE BIRTH</h2>
    <p class="services">4D Ultrasound<span class="dot">•</span>Pregnancy Confirmation<span class="dot">•</span>Early Gender</p>
    <div class="brand-box">
      <div class="brand-name">4D Cradle Glimpse</div>
      <div class="brand-rule"></div>
      <div class="brand-tag">PRENATAL ULTRASOUND STUDIO</div>
    </div>
    <div class="contact">
      <svg class="pin" viewBox="0 0 20 26"><path d="M10 0C4.5 0 0 4.4 0 9.8 0 17 10 26 10 26s10-9 10-16.2C20 4.4 15.5 0 10 0z" fill="var(--pin-gold)"/><circle cx="10" cy="9.5" r="3.6" fill="var(--paper)"/></svg>
      <div class="city">Cedar Bay Florida</div>
      <div class="phone">850-471-5923</div>
    </div>
  </section>
</body>
</html>
```